VFX Company Business Card Design Project

The Kestrel Works is a decentralized Visual Effects Studio servicing the television and feature film industries.
Project Brief:
Take our logo that was previously designed on Pencil Harbor and make a double sided business card.
Requirements:
- Card MUST be double sided.
- Front of card MUST have the yellow part of our logo against the dark grey background.
- Back of card is completely up to the designer.
- Back of card must include the complete company logo.
Please follow these File Preparation guidelines:
http://printnook.ca/infopage?file=filetype_en&s=PrintNook_new&lang=en
Business

```html
<!DOCTYPE html>
<html lang="en">
<head>
<meta charset="utf-8">
<title>The Kestrel Works – Business Card</title>
<link rel="stylesheet" href="https://fonts.googleapis.com/css2?family=Open+Sans:wght@400;600;700&display=swap">
<style>
  :root {
    --backdrop: #e4e2de;
    --card-dark: #2a2a2c;
    --brand-yellow: #f2be22;
    --band-grey: #a9a9ab;
    --text-light: #ffffff;
    --text-soft: #e2e2e2;
  }
  * { box-sizing: border-box; margin: 0; padding: 0; }
  html, body {
    width: 1200px; height: 900px; overflow: hidden;
    background: var(--backdrop);
    font-family: "Open Sans", Arial, sans-serif;
  }
  .canvas { position: relative; width: 1200px; height: 900px; }
  .card {
    position: absolute; left: 260px;
    width: 680px; height: 388px;
    background: var(--card-dark);
    border-radius: 4px;
    overflow: hidden;
    box-shadow: 0 10px 28px rgba(0,0,0,0.22);
  }
  .card--front { top: 50px; }
  .card--back { top: 462px; }

  /* Front: brand name on dark */
  .front-brand {
    position: absolute; inset: 0;
    display: flex; align-items: center; justify-content: center; gap: 26px;
  }
  .front-brand__dot {
    width: 70px; height: 70px; border-radius: 50%;
    background: var(--brand-yellow);
  }
  .front-brand__name {
    color: var(--brand-yellow);
    font-weight: 700; font-size: 54px; letter-spacing: 0.5px;
  }

  /* Back: artwork band + details */
  .back-artwork {
    position: absolute; left: 0; right: 0; bottom: 0; height: 84px;
    background: linear-gradient(90deg, var(--brand-yellow) 0%, var(--brand-yellow) 55%, var(--band-grey) 100%);
  }
  .back-brand {
    position: absolute; left: 34px; top: 30px;
    display: flex; align-items: center; gap: 12px;
  }
  .back-brand__dot {
    width: 26px; height: 26px; border-radius: 50%;
    background: var(--brand-yellow);
  }
  .back-brand__name {
    color: var(--text-light);
    font-weight: 600; font-size: 26px;
  }
  .contact {
    position: absolute; right: 34px; top: 112px;
    text-align: right; color: var(--text-soft);
  }
  .contact__name {
    color: var(--text-light); font-weight: 700; font-size: 25px; line-height: 1.1;
  }
  .contact__role {
    color: var(--text-light); font-size: 14px; font-weight: 600; margin-bottom: 10px;
  }
  .contact__line {
    display: flex; justify-content: flex-end; align-items: center; gap: 8px;
    font-size: 13.5px; line-height: 21px;
  }
  .contact__icon { width: 12px; height: 12px; flex: none; }
</style>
</head>
<body>
<main class="canvas">

  <section class="card card--front" aria-label="Card front">
    <div class="front-brand">
      <span class="front-brand__dot"></span>
      <span class="front-brand__name">The Kestrel Works</span>
    </div>
  </section>

  <section class="card card--back" aria-label="Card back">
    <div class="back-artwork" role="img" aria-label="Decorative yellow and grey wave band along the lower edge"></div>

    <div class="back-brand">
      <span class="back-brand__dot"></span>
      <span class="back-brand__name">The Kestrel Works</span>
    </div>

    <div class="contact">
      <p class="contact__name">Dana Whitfield</p>
      <p class="contact__role">President</p>
      <p class="contact__line">P.O Box 4170, Millbrook AU 3KT
        <svg class="contact__icon" viewBox="0 0 12 12"><path fill="var(--brand-yellow)" d="M6 0.5a4 4 0 0 0-4 4c0 3 4 7 4 7s4-4 4-7a4 4 0 0 0-4-4zm0 5.6a1.6 1.6 0 1 1 0-3.2 1.6 1.6 0 0 1 0 3.2z"/></svg>
      </p>
      <p class="contact__line">+01 555 01942
        <svg class="contact__icon" viewBox="0 0 12 12"><path fill="var(--brand-yellow)" d="M2.6 0.8l1.8 2.3-1 1.2c.7 1.6 2 2.9 3.6 3.6l1.2-1 2.3 1.8-1 2.2C5 10.7 1.3 7 .4 1.8z"/></svg>
      </p>
      <p class="contact__line">hello@kestrelworks.net
        <svg class="contact__icon" viewBox="0 0 12 12"><rect x="0.5" y="2" width="11" height="8" rx="1" fill="var(--brand-yellow)"/><path d="M1 2.6l5 4 5-4" stroke="var(--card-dark)" stroke-width="1.1" fill="none"/></svg>
      </p>
      <p class="contact__line">www.kestrelworks.net
        <svg class="contact__icon" viewBox="0 0 12 12"><circle cx="6" cy="6" r="5" fill="none" stroke="var(--brand-yellow)" stroke-width="1.4"/><path d="M1 6h10M6 1c-2.4 2.8-2.4 7.2 0 10M6 1c2.4 2.8 2.4 7.2 0 10" stroke="var(--brand-yellow)" stroke-width="1" fill="none"/></svg>
      </p>
    </div>
  </section>

</main>
</body>
</html>
```